Email Signature and a letter head

I need a professional email signature and a letter head for letters sent by post. I've attached my logo and a signature i am currently using. Current letter head is also attached.

Target Market(s)

Accounting Clients

Industry/Entity Type

Public Accounting

Font styles to use
Sans Serif

Colors

Designer to choose colors to be used in the design.

Requirements
Must have
• My logo, RM Logo, Lumo Logo, Tax Agent logo. All attached.
• All my credentials - examples in the attached documents

```html
<!DOCTYPE html>
<html lang="en">
<head>
<meta charset="utf-8">
<title>Beacon Hill Business Services – Letterhead and Email Signature</title>
<link rel="stylesheet" href="https://fonts.googleapis.com/css2?family=Roboto:ital,wght@0,400;0,500;0,700;1,400&family=Cinzel:wght@500&display=swap">
<style>
  :root{
    --gold:#b8952b;
    --gold-soft:#cfae4e;
    --ink:#2f2f2f;
    --grey:#555555;
    --rule:#8a8a8a;
    --paper:#ffffff;
    --stage:#2a2a2a;
  }
  *{box-sizing:border-box;margin:0;padding:0}
  html,body{width:1200px;height:957px;overflow:hidden;background:var(--stage)}
  body{font-family:"Roboto",sans-serif;color:var(--ink);position:relative}

  /* ---------- Letterhead ---------- */
  .letterhead{position:absolute;left:40px;top:40px;width:620px;height:877px;
    background:linear-gradient(#ffffff 0%,#ffffff 55%,#f1f1f1 100%);}
  .letterhead .tab{position:absolute;left:64px;top:0;width:52px;height:43px;background:var(--gold)}
  .brand{position:absolute;display:flex;flex-direction:column;align-items:center;
    font-family:"Roboto",sans-serif;font-weight:500;color:var(--gold);text-align:center;line-height:1.1}
  .brand .dot{width:44px;height:44px;border:2px solid var(--gold);border-radius:50%;margin-bottom:6px}
  .letterhead .brand{left:20px;top:52px;width:140px;font-size:12px;letter-spacing:.5px}
  .brand small{font-size:7px;letter-spacing:1.5px;display:block;margin-top:2px}

  .badges{position:absolute;left:375px;top:44px;display:flex;align-items:center;gap:6px}
  .badges .badge{width:34px;height:34px;border-radius:50%}
  .badge.square{width:30px;height:30px;border-radius:4px;background:#d9d9d9}
  .badge.teal{background:#1aa9d6}
  .badge.dark{background:#1d7e95}
  .badge.seal{background:#fff;border:3px solid #9bbf3a}
  .badges .partner{font-size:11px;font-weight:500;color:#1aa9d6}
  .badges .agent{font-size:6px;color:#444;line-height:1.2}

  .letter{position:absolute;left:68px;top:206px;width:484px;font-size:9.6px;line-height:12.4px;color:#333}
  .letter .date{margin-bottom:22px}
  .letter .salute{font-weight:700;margin-bottom:10px}
  .letter p{text-align:justify;margin-bottom:11px}
  .letter .close{margin-top:24px}
  .sign-mark{display:block;width:130px;height:22px;margin-top:8px;
    background:linear-gradient(90deg,#d6d6d6,#eeeeee)}
  .letter .role{line-height:12px}
  .letter .company{font-weight:700}

  .letter-foot{position:absolute;left:32px;right:32px;top:803px;border-top:1px solid var(--rule);
    display:flex;font-size:9.6px;line-height:12.4px;color:#333;padding-top:14px}
  .letter-foot .col{position:relative}
  .letter-foot .col::before{content:"";position:absolute;top:-16px;left:0;width:16px;height:3px;background:var(--gold)}
  .letter-foot .contact{width:265px}
  .letter-foot .cred{width:129px}
  .ico{display:inline-block;width:8px;height:8px;margin-right:4px;vertical-align:-1px}
  .ico svg{width:8px;height:8px;display:block}

  .bar{position:absolute;left:0;right:0;bottom:0;height:7px;
    background:linear-gradient(90deg,var(--gold) 0,var(--gold) 50%,var(--grey) 50%,var(--grey) 100%)}

  /* ---------- Email signature ---------- */
  .signature{position:absolute;left:676px;width:504px;height:124px;background:var(--paper);overflow:hidden}
  .signature.first{top:290px}
  .signature.second{top:500px}
  .signature .brand{left:12px;top:12px;width:110px;font-size:11px}
  .signature .brand .dot{width:40px;height:40px;margin-bottom:4px}
  .signature .brand small{font-size:6px}
  .person{position:absolute;left:138px;top:12px;font-size:10px;line-height:12.5px;color:#333}
  .person .name{font-family:"Cinzel",serif;font-weight:500;color:var(--gold);font-size:14px;line-height:15px;letter-spacing:.5px}
  .person .title{font-style:italic}
  .sig-contact{position:absolute;left:272px;top:15px;font-size:9.6px;line-height:12.4px;color:#333}
  .liability{position:absolute;left:133px;right:0;top:60px;height:19px;background:var(--gold);
    border-left:5px solid var(--grey);color:#fff;font-size:9px;line-height:19px;padding-left:6px;
    white-space:nowrap;overflow:hidden}
  .disclaimer{position:absolute;left:0;right:0;top:86px;text-align:center;font-size:9.6px;line-height:10.5px;color:#333}
</style>
</head>
<body>

<svg width="0" height="0" style="position:absolute" aria-hidden="true">
  <defs>
    <symbol id="i-phone" viewBox="0 0 10 10"><path d="M2 1l2 2-1 1.2c.6 1.2 1.6 2.2 2.8 2.8L7 6l2 2-1.3 1.3C4.5 9 1 5.5.7 2.3z" fill="#b8952b"/></symbol>
    <symbol id="i-mail" viewBox="0 0 10 10"><rect x=".6" y="2" width="8.8" height="6" fill="none" stroke="#b8952b" stroke-width="1"/><path d="M.8 2.3L5 5.6l4.2-3.3" fill="none" stroke="#b8952b" stroke-width="1"/></symbol>
    <symbol id="i-web" viewBox="0 0 10 10"><circle cx="5" cy="5" r="4.3" fill="#b8952b"/></symbol>
  </defs>
</svg>

<!-- Letterhead -->
<section class="letterhead">
  <div class="tab"></div>
  <div class="brand"><span class="dot"></span>Beacon Hill<small>Business Services</small></div>

  <div class="badges">
    <span class="badge square" role="img" aria-label="Professional body badge"></span>
    <span class="badge teal"></span><span class="partner">Lumo</span>
    <span class="badge dark" role="img" aria-label="Certified advisor badge"></span>
    <span class="badge seal" role="img" aria-label="Registered tax agent badge"></span>
    <span class="agent">Tax agent<br>10020030</span>
  </div>

  <article class="letter">
    <div class="date">January 01, 2020</div>
    <div class="salute">Dear Henrik Solberg,</div>
    <p>Lorem ipsum dolor sit amet, consectetuer adipiscing elit, sed diam nonummy nibh euismod tincidunt ut laoreet dolore magna aliquam erat volutpat. Ut wisi enim ad minim veniam, quis nostrud exerci tation ullamcorper suscipit lobortis nisl ut aliquip ex ea commodo consequat. Duis dolore te feugait nulla facilisi. Nam liber tempor cum soluta nobis eleifend option congue nihil imperdiet doming id quod mazim placerat facer possim assum. Duis autem vel eum iriure dolor in hendrerit in vulputate velit esse molestie consequat, vel illum dolore eu feugiat nulla facilisis at vero eros et accumsan et iusto odio dignissim qui blandit praesent luptatum zzril delenit augue duis dolore te feugait nulla facilisi. Consectetuer adipiscing elit, sed diam nonummy nibh euismod tincidunt ut laoreet dolore magna aliquam erat volutpat. Ut wisi enim ad minim veniam, quis nostrud exerci tation ullamcorper suscipit lobortis nisl ut aliquip ex ea commodo consequat.</p>
    <p>Consectetuer adipiscing elit, sed diam nonummy nibh euismod tincidunt ut laoreet dolore magna aliquam erat volutpat. Ut wisi enim ad minim veniam, quis nostrud exerci tation ullamcorper suscipit lobortis nisl ut aliquip ex ea commodo consequat. Consectetuer adipiscing elit, sed diam nonummy nibh euismod tincidunt ut laoreet dolore magna aliquam erat volutpat. Ut wisi enim ad minim veniam, quis nostrud exerci tation ullamcorper suscipit lobortis nisl ut aliquip ex ea commodo consequat.</p>
    <p>Dolor sit amet, consectetuer adipiscing elit, sed diam nonummy nibh euismod tincidunt ut laoreet dolore magna aliquam erat volutpat. Ut wisi enim ad minim veniam, quis nostrud exerci tation ullamcorper suscipit lobortis nisl ut aliquip ex ea commodo consequat. Duis dolore te feugait nulla facilisi. Nam liber tempor cum soluta nobis eleifend option congue nihil imperdiet doming id quod mazim placerat facer possim assum. Duis dolore te feugait nulla facilisi. Nam liber tempor cum soluta nobis eleifend option congue nihil imperdiet doming id quod mazim placerat facer possim assum. Duis dolore te feugait nulla facilisi. Nam liber tempor cum soluta nobis eleifend option congue nihil imperdiet doming id quod mazim placerat facer possim assum.</p>
    <div class="close">Sincerely Yours,</div>
    <span class="sign-mark" role="img" aria-label="Handwritten signature of Owen Pratt"></span>
    <div class="role">Authorized Managing Director</div>
    <div class="company">Your Company Name</div>
  </article>

  <footer class="letter-foot">
    <div class="col contact">
      <div><span class="ico"><svg><use href="#i-phone"/></svg></span>041 555 0193</div>
      <div><span class="ico"><svg><use href="#i-mail"/></svg></span>marlow@beaconhillbusiness.com.au</div>
      <div><span class="ico"><svg><use href="#i-web"/></svg></span>www.beaconhillbusiness.com.au</div>
    </div>
    <div class="col cred">
      <div>Marlow Keane RM BBus</div>
      <div>ABN: 12 345 678 901</div>
      <div>TAN: 100 200 30</div>
    </div>
    <div class="col address">
      <div>Beacon Hill Business Services</div>
      <div>18 Larkfield Road</div>
      <div>Seaview VIC 3100</div>
    </div>
  </footer>
  <div class="bar"></div>
</section>

<!-- Email signatures -->
<section class="signature first">
  <div class="brand"><span class="dot"></span>Beacon Hill<small>Business Services</small></div>
  <div class="person">
    <div class="name">Marlow Keane</div>
    <div>Principal</div>
    <div class="title">Chartered Accountant</div>
  </div>
  <div class="sig-contact">
    <div><span class="ico"><svg><use href="#i-phone"/></svg></span>041 555 0193</div>
    <div><span class="ico"><svg><use href="#i-mail"/></svg></span>marlow@beaconhillbusiness.com.au</div>
    <div><span class="ico"><svg><use href="#i-web"/></svg></span>www.beaconhillbusiness.com.au</div>
  </div>
  <div class="liability">Liability limited by a scheme approved under Professional Standards Legislation.</div>
  <div class="disclaimer">This e-mail and its attachments are confidential and privileged. Any unauthorized use is expressly<br>prohibited. If you receive this e-mail in error please contact us, then delete the e-mail.</div>
  <div class="bar"></div>
</section>

<section class="signature second">
  <div class="brand"><span class="dot"></span>Beacon Hill<small>Business Services</small></div>
  <div class="person">
    <div class="name">Marlow Keane</div>
    <div>Principal</div>
    <div class="title">Chartered Accountant</div>
  </div>
  <div class="sig-contact">
    <div><span class="ico"><svg><use href="#i-phone"/></svg></span>041 555 0193</div>
    <div><span class="ico"><svg><use href="#i-mail"/></svg></span>marlow@beaconhillbusiness.com.au</div>
    <div><span class="ico"><svg><use href="#i-web"/></svg></span>www.beaconhillbusiness.com.au</div>
  </div>
  <div class="liability">Liability limited by a scheme approved under Professional Standards Legislation.</div>
  <div class="disclaimer">This e-mail and its attachments are confidential and privileged. Any unauthorized use is expressly<br>prohibited. If you receive this e-mail in error please contact us, then delete the e-mail.</div>
  <div class="bar"></div>
</section>

</body>
</html>
```